KVOR Individual and Corporate Development Business Card Design

KVOR needs a business card design that is aligned with it's values and targetted markets. Coherent Lattice of Adaptive Reasoning Method's self diagnosis model and tools, which can be used for personal improvement and team/business performance enhancement, is based on the learnings of over 20 years of medical practitioning. KVOR supercharges personal effectiveness and awareness to also increase team and business performance.

The targetted markets are high performance individuals and teams who aspire seek to enhance their capabilities and achieve their absolute best potential.

Look and feel for the business card design we are looking for is high technology, premium, fresh, new and medical.

Target Market(s)

Industry/Entity Type

Business Consultant

Contact Information for Business Card

Logo, Full Name, Title, Phone number, Email, company name, Address,

Font styles to use
Sans Serif

Requirements
Must have
• Tag line: Amplifying Potential for Driven, Focused Achievers
• Please use same colours as the logo.

```html
<!DOCTYPE html>
<html lang="en">
<head>
<meta charset="utf-8">
<title>KVOR Business Card</title>
<link href="https://fonts.googleapis.com/css2?family=Roboto:ital,wght@0,400;0,500;0,700;1,400&family=Roboto+Condensed:wght@700&display=swap" rel="stylesheet">
<style>
  :root {
    --teal: #02a8c0;
    --ink: #555759;
    --slate: #5c5f64;
    --paper: #f4f4f4;
    --white: #ffffff;
    --backdrop: #222324;
  }
  * { margin: 0; padding: 0; box-sizing: border-box; }
  html, body { width: 1200px; height: 960px; overflow: hidden; }
  body {
    position: relative;
    background: var(--backdrop);
    font-family: "Roboto", Arial, sans-serif;
  }
  .card {
    position: absolute;
    width: 600px;
    height: 343px;
    overflow: hidden;
  }
  .card-front { left: 314px; top: 113px; background: var(--paper); }
  .card-back { left: 311px; top: 472px; background: var(--teal); }

  .brand { position: absolute; display: flex; flex-direction: column; }
  .brand-row { display: flex; align-items: center; gap: 12px; }
  .brand-dot { width: 18px; height: 18px; border-radius: 50%; background: currentColor; }
  .brand-name { font-weight: 700; font-size: 56px; letter-spacing: 4px; line-height: 1; }
  .brand-full { font-weight: 700; font-size: 13px; line-height: 15px; letter-spacing: 0.3px; text-transform: uppercase; margin-top: 6px; }
  .card-front .brand { left: 33px; top: 52px; color: var(--teal); }
  .card-back .brand { left: 0; right: 0; top: 134px; align-items: center; color: var(--white); text-align: center; }
  .card-back .brand-name { font-size: 64px; }
  .card-back .brand-full { font-size: 15px; line-height: 17px; margin-top: 8px; }

  .company {
    position: absolute; left: 33px; top: 179px;
    color: var(--ink); font-size: 14px; font-weight: 500; line-height: 18px;
  }
  .address {
    position: absolute; left: 33px; top: 219px;
    color: var(--ink); font-size: 15px; line-height: 18px;
  }
  .contacts { position: absolute; left: 33px; top: 263px; list-style: none; }
  .contacts li {
    display: flex; align-items: center; gap: 7px;
    color: var(--ink); font-size: 15px; line-height: 19.5px;
  }
  .contacts svg { width: 13px; height: 13px; fill: var(--teal); }

  .person { position: absolute; right: 33px; top: 227px; text-align: right; }
  .person-name {
    font-family: "Roboto Condensed", Arial, sans-serif;
    font-weight: 700; font-size: 21px; color: var(--teal); line-height: 24px;
  }
  .person-title { font-size: 15px; font-weight: 500; color: var(--ink); margin-top: 4px; }

  .band { position: absolute; left: 0; bottom: 0; width: 600px; height: 15px; }

  .tagline {
    position: absolute; left: 0; right: 0; top: 292px;
    text-align: center; color: var(--white);
    font-style: italic; font-size: 14px;
  }
</style>
</head>
<body>
  <section class="card card-front">
    <div class="brand">
      <div class="brand-row"><span class="brand-name">KVOR</span><span class="brand-dot"></span></div>
      <span class="brand-full">Coherent Lattice Of<br>Adaptive Reasoning Method</span>
    </div>

    <p class="company">Coherent Lattice Of<br>Adaptive Reasoning Method</p>
    <p class="address">2140 Larkspur Way<br>Fairbanks, Alaska 99701</p>

    <ul class="contacts">
      <li><svg viewBox="0 0 16 16"><path d="M3.6 1.2l2.3 2.9-1.3 1.8c.9 2 2.5 3.6 4.5 4.5l1.8-1.3 2.9 2.3-1.4 2.7C6.6 14.2 1.8 9.4 .9 3z"/></svg>907 555 0142</li>
      <li><svg viewBox="0 0 16 16"><path d="M1 3h14v1.2L8 9 1 4.2zM1 6l7 4.8L15 6v7H1z"/></svg>dana@kvorgroup.com</li>
      <li><svg viewBox="0 0 16 16"><circle cx="8" cy="8" r="7"/></svg>www.kvorgroup.com</li>
    </ul>

    <div class="person">
      <p class="person-name">DANA WHITLOW</p>
      <p class="person-title">CEO/FOUNDER</p>
    </div>

    <svg class="band" viewBox="0 0 600 15" preserveAspectRatio="none">
      <polygon points="0,0 422,0 417,15 0,15" fill="var(--teal)"/>
      <polygon points="426,0 600,0 600,15 421,15" fill="var(--slate)"/>
    </svg>
  </section>

  <section class="card card-back">
    <div class="brand">
      <div class="brand-row"><span class="brand-name">KVOR</span><span class="brand-dot"></span></div>
      <span class="brand-full">Coherent Lattice Of<br>Adaptive Reasoning Method</span>
    </div>
    <p class="tagline">Amplifying Potential for Driven, Focused Achievers</p>
  </section>
</body>
</html>
```